Business Card Design - Amberfield Court

We are looking at a new design for our business cards that has a modern and professional look. We run a residential aged care facility focussing on the care of residents. The cards will be used for potential clients, consultants and business opportunities in this sector. Blue and white is our main colours and would to see these colours incorporated in the design.
Industry/Entity Type
Business
Contact Information for Business Card
Amberfield Court, Darren Walsh, dwalsh@amberfieldcourt.com.au, Finance Manager, 0472 639 208, BCom, 37 Marrabel Crescent, Brindle Vale, Qld 4093.
Look and feel
Each slider illustrates characteristics of the customer's brand and the style your logo design should communicate.

```html
<!DOCTYPE html>
<html lang="en">
<head>
<meta charset="utf-8">
<title>Amberfield Court – Business Card</title>
<link rel="stylesheet" href="https://fonts.googleapis.com/css2?family=Arimo:wght@400;700&display=swap">
<style>
  :root{
    --stage:#e9e7e4;
    --card:#ffffff;
    --card-shade:#ececec;
    --brand-blue:#4a7a94;
    --brand-blue-dark:#3d6980;
    --taupe:#a69b95;
    --ink:#555555;
    --rule:#d4d4d4;
  }
  *{box-sizing:border-box;margin:0;padding:0}
  html,body{width:1200px;height:950px;overflow:hidden}
  body{background:var(--stage);font-family:"Arimo",Arial,sans-serif;position:relative}

  .card{
    position:absolute;left:250px;width:700px;height:428px;
    background:linear-gradient(160deg,var(--card) 40%,var(--card-shade) 100%);
    border-radius:20px;overflow:hidden;
    box-shadow:0 8px 24px rgba(0,0,0,.16);
  }
  .card-back{top:30px}
  .card-front{top:492px}

  .waves{position:absolute;left:0;bottom:0;width:700px;height:150px}

  /* back side */
  .back-brand{
    position:absolute;left:0;right:0;top:70px;
    display:flex;flex-direction:column;align-items:center;gap:20px;
  }
  .back-brand .brand-dot{width:120px;height:120px}
  .back-brand .brand-name{font-size:30px;letter-spacing:3px}

  /* front side */
  .front-brand{
    position:absolute;left:30px;top:86px;width:260px;
    display:flex;flex-direction:column;align-items:center;gap:18px;
  }
  .front-brand .brand-dot{width:100px;height:100px}
  .front-brand .brand-name{font-size:21px;letter-spacing:1px}

  .brand-dot{border-radius:50%;background:var(--brand-blue)}
  .brand-name{
    font-weight:400;text-transform:uppercase;color:var(--brand-blue);
    text-align:center;white-space:nowrap;
  }

  .divider{position:absolute;left:310px;top:78px;width:1px;height:190px;background:var(--rule)}

  .contact{position:absolute;left:332px;top:78px;color:var(--ink)}
  .contact-name{font-size:24px;font-weight:700;color:var(--brand-blue);line-height:1.2}
  .contact-name .credential{font-size:17px}
  .contact-role{font-size:17px;color:var(--taupe);margin-top:2px}
  .contact-address{font-size:17px;line-height:1.3;margin-top:12px}
  .contact-lines{list-style:none;margin-top:8px;font-size:17px;line-height:1.5}
  .contact-lines li{display:flex;align-items:center;gap:9px}
  .contact-lines svg{width:16px;height:16px;flex:none;fill:var(--brand-blue)}
</style>
</head>
<body>
  <article class="card card-back">
    <div class="back-brand">
      <div class="brand-dot"></div>
      <div class="brand-name">Amberfield Court</div>
    </div>
    <svg class="waves" viewBox="0 0 700 150" preserveAspectRatio="none" aria-hidden="true">
      <path d="M0 28 C175 102 420 116 700 75 L700 85 C420 124 182 116 0 45 Z" fill="var(--taupe)"/>
      <path d="M0 52 C182 123 420 131 700 93 L700 150 L0 150 Z" fill="var(--brand-blue)"/>
      <path d="M0 52 C182 123 420 131 700 93 L700 100 C420 137 182 130 0 63 Z" fill="var(--brand-blue-dark)" opacity=".35"/>
    </svg>
  </article>

  <article class="card card-front">
    <div class="front-brand">
      <div class="brand-dot"></div>
      <div class="brand-name">Amberfield Court</div>
    </div>

    <div class="divider"></div>

    <section class="contact">
      <h1 class="contact-name">Darren Walsh <span class="credential">BCom</span></h1>
      <p class="contact-role">Finance Manager</p>
      <p class="contact-address">37 Marrabel Crescent<br>Brindle Vale, Qld 4093.</p>
      <ul class="contact-lines">
        <li>
          <svg viewBox="0 0 24 24"><path d="M6.6 10.8a15.1 15.1 0 0 0 6.6 6.6l2.2-2.2a1 1 0 0 1 1-.25 11.4 11.4 0 0 0 3.6.57 1 1 0 0 1 1 1V20a1 1 0 0 1-1 1A17 17 0 0 1 3 4a1 1 0 0 1 1-1h3.5a1 1 0 0 1 1 1c0 1.25.2 2.45.57 3.6a1 1 0 0 1-.25 1z"/></svg>
          0472 639 208
        </li>
        <li>
          <svg viewBox="0 0 24 24"><path d="M2 5h20v14H2z M3.5 6.5 12 13l8.5-6.5" fill="none" stroke="#4a7a94" stroke-width="2"/><path d="M2 5h20L12 12.5z"/></svg>
          dwalsh@amberfieldcourt.com.au
        </li>
        <li>
          <svg viewBox="0 0 24 24"><circle cx="12" cy="12" r="10"/><path d="M2 12h20M12 2c3 3 3 17 0 20M12 2c-3 3-3 17 0 20" fill="none" stroke="#fff" stroke-width="1.5"/></svg>
          www.amberfieldcourt.com.au
        </li>
      </ul>
    </section>

    <svg class="waves" viewBox="0 0 700 150" preserveAspectRatio="none" aria-hidden="true">
      <path d="M0 28 C175 102 420 116 700 75 L700 85 C420 124 182 116 0 45 Z" fill="var(--taupe)"/>
      <path d="M0 52 C182 123 420 131 700 93 L700 150 L0 150 Z" fill="var(--brand-blue)"/>
      <path d="M0 52 C182 123 420 131 700 93 L700 100 C420 137 182 130 0 63 Z" fill="var(--brand-blue-dark)" opacity=".35"/>
    </svg>
  </article>
</body>
</html>
```